Brand new letterhead, business card, email signature etc.

We are a financial company in London, UK. Our website is www.marlowvane.com. We're wanting a complete remodel of the company colours, letter head, business cards, email signatures, etc. Looking to keep the same font for the company name. I have upload a colour palette that we want to work with. We're looking for company letterhead for outgoing letters/ correspondence, letterhead for internal documentation, email signatures, e-letters. etc. Ultimately we will redesign the entire website also. It is important that our clients get a strong, secure, warm, trustworthy, solid feeling and first impression.
Updates

Designs look the same

Target Market(s)

Institutional investors, (ultra) high net worth individuals

Industry/Entity Type

Finance, Invesments banking.

Font styles to use
Other font styles liked:
• Current font is "Champagne & Limousines"

Requirements
Must have
• Must use the colours provided on the PDF uploaded to the portal. The purple = main colour. The red = accent colour.
Nice to have
• Nice to use same font as now for the company name "Corvane". Font is "Champagne & Limousines". Nice to have some reference to the old logo flower, but only subtle.
Should not have
• Do not use the colour red from our website. Use the colours provided on the colour palette PDF that I uploaded in the portal.

```html
<!DOCTYPE html>
<html lang="en">
<head>
<meta charset="utf-8">
<title>Corvane Stationery</title>
<link rel="stylesheet" href="https://fonts.googleapis.com/css2?family=Josefin+Sans:wght@300;400;600&display=swap">
<style>
  :root {
    --plum: #25001a;
    --accent: #d42a16;
    --paper: #f4f4f2;
    --ink: #2b2b2b;
    --muted: #6a6a6a;
    --backdrop: #e4e4e6;
  }
  * { margin: 0; padding: 0; box-sizing: border-box; }
  html, body { width: 1200px; height: 792px; overflow: hidden; }
  body {
    background: var(--backdrop);
    font-family: "Josefin Sans", sans-serif;
    color: var(--ink);
    position: relative;
  }
  .sheet { position: absolute; background: var(--paper); overflow: hidden; }

  /* brand lockup */
  .brand { position: absolute; left: 0; right: 0; display: flex; align-items: center; justify-content: center; gap: 7px; }
  .brand-mark { border: 1px solid var(--plum); flex: none; }
  .brand-name { font-weight: 300; color: var(--plum); letter-spacing: 0.22em; line-height: 1; }

  /* business card front */
  .card-front { left: 184px; top: 131px; width: 170px; height: 97px; background: var(--plum); }
  .card-front .band { position: absolute; left: 0; right: 0; top: 29px; height: 39px; background: var(--paper); }
  .card-front .brand { top: 8px; }
  .card-front .brand-mark { width: 16px; height: 16px; }
  .card-front .brand-name { font-size: 13px; }

  /* business card back & compliments slip */
  .frame { position: absolute; border: 1.5px solid var(--plum); }
  .card-back { left: 379px; top: 131px; width: 170px; height: 97px; }
  .card-back .frame { inset: 6px; }
  .card-back .brand { top: 26px; }
  .card-back .brand-mark { width: 12px; height: 12px; }
  .card-back .brand-name { font-size: 9px; }

  .contact-strip { position: absolute; left: 50%; transform: translateX(-50%); color: var(--accent); text-align: center; }
  .contact-strip .row { border-top: 0.6px solid var(--plum); }
  .contact-strip .row:last-child { border-bottom: 0.6px solid var(--plum); display: flex; }
  .contact-strip .row:last-child span { flex: 1; }
  .contact-strip .row:last-child span + span { border-left: 0.6px solid var(--plum); }

  .card-back .contact-strip { top: 64px; width: 100px; font-size: 3.6px; line-height: 7.5px; }

  .slip { left: 184px; top: 255px; width: 365px; height: 182px; }
  .slip .frame { inset: 13px 14px; }
  .slip .brand { top: 45px; }
  .slip .brand-mark { width: 30px; height: 28px; }
  .slip .brand-name { font-size: 16px; }
  .slip .contact-strip { top: 131px; width: 132px; font-size: 5px; line-height: 10.5px; }

  /* envelope */
  .envelope { left: 184px; top: 468px; width: 365px; height: 182px; }
  .envelope .flap { position: absolute; left: 0; top: 0; width: 365px; height: 48px; }
  .envelope .brand { top: 81px; }
  .envelope .brand-mark { width: 38px; height: 34px; }
  .envelope .brand-name { font-size: 19px; }

  /* letterhead */
  .letterhead { left: 595px; top: 131px; width: 367px; height: 519px; }
  .letterhead .corner { position: absolute; }
  .letterhead .brand { top: 40px; }
  .letterhead .brand-mark { width: 34px; height: 30px; }
  .letterhead .brand-name { font-size: 17px; }
  .watermark {
    position: absolute; left: 95px; top: 137px; width: 190px; height: 230px;
    background: radial-gradient(ellipse at center, rgba(37,0,26,0.05), rgba(37,0,26,0) 70%);
  }
  .sender { position: absolute; left: 41px; top: 136px; padding-left: 5px; border-left: 0.8px solid var(--plum); }
  .sender .name { font-size: 7px; font-weight: 600; color: var(--plum); letter-spacing: -0.01em; }
  .sender .role { font-size: 4.4px; letter-spacing: 0.22em; color: var(--muted); margin-bottom: 5px; }
  .sender .line { font-size: 4.2px; line-height: 7.4px; color: var(--ink); }
  .label { color: var(--accent); }
  .date { position: absolute; right: 40px; top: 177px; font-size: 5px; }
  .body-copy { position: absolute; left: 41px; top: 209px; width: 286px; font-size: 6.9px; font-weight: 300; line-height: 8.1px; text-align: justify; color: #3a3a3a; }
  .body-copy p + p { margin-top: 8px; }
  .signoff { position: absolute; right: 40px; top: 360px; text-align: right; }
  .signoff .signature { width: 66px; height: 22px; margin-left: auto; background: linear-gradient(90deg, rgba(37,0,26,0), rgba(37,0,26,0.08)); }
  .signoff .name { font-size: 7.6px; font-weight: 600; color: var(--plum); letter-spacing: 0.06em; margin-top: 4px; }
  .signoff .role { font-size: 4.6px; letter-spacing: 0.3em; color: var(--muted); }
  .footer-contacts { position: absolute; left: 40px; top: 428px; font-size: 5.6px; line-height: 6.4px; color: #333; }
  .footer-contacts .item { display: flex; align-items: center; gap: 8px; height: 18px; margin-bottom: 2px; }
  .footer-contacts svg { width: 9px; height: 9px; flex: none; }
</style>
</head>
<body>

  <!-- business card, front -->
  <section class="sheet card-front">
    <div class="band">
      <div class="brand"><span class="brand-mark"></span><span class="brand-name">CORVANE</span></div>
    </div>
  </section>

  <!-- business card, back -->
  <section class="sheet card-back">
    <div class="frame"></div>
    <div class="brand"><span class="brand-mark"></span><span class="brand-name">CORVANE</span></div>
    <div class="contact-strip">
      <div class="row">14 Garnet Row, London EC2A 4PL, UK</div>
      <div class="row"><span>www.marlowvane.com</span><span>info@marlowvane.com</span></div>
    </div>
  </section>

  <!-- compliments slip -->
  <section class="sheet slip">
    <div class="frame"></div>
    <div class="brand"><span class="brand-mark"></span><span class="brand-name">CORVANE</span></div>
    <div class="contact-strip">
      <div class="row">14 Garnet Row, London EC2A 4PL, UK</div>
      <div class="row"><span>www.marlowvane.com</span><span>info@marlowvane.com</span></div>
    </div>
  </section>

  <!-- envelope -->
  <section class="sheet envelope">
    <svg class="flap" viewBox="0 0 365 48" aria-hidden="true">
      <path d="M0 0 H365 L361 30 Q359 46 345 46 H20 Q6 46 4 30 Z" fill="var(--plum)"/>
    </svg>
    <div class="brand"><span class="brand-mark"></span><span class="brand-name">CORVANE</span></div>
  </section>

  <!-- letterhead -->
  <section class="sheet letterhead">
    <svg class="corner" style="left:0;top:0" width="367" height="110" viewBox="0 0 367 110" aria-hidden="true">
      <polygon points="0,0 71,0 0,71" fill="var(--plum)"/>
      <line x1="89" y1="0" x2="0" y2="89" stroke="var(--accent)" stroke-width="6"/>
      <line x1="73" y1="34" x2="0" y2="107" stroke="var(--plum)" stroke-width="5"/>
      <polygon points="46,24 342,24 336,30 46,30" fill="var(--accent)"/>
      <line x1="78" y1="19" x2="251" y2="19" stroke="var(--plum)" stroke-width="1.6"/>
    </svg>

    <div class="brand"><span class="brand-mark"></span><span class="brand-name">CORVANE</span></div>

    <div class="watermark" role="img" aria-label="Faint brand emblem watermark"></div>

    <div class="sender">
      <div class="name">ELENA R. WHITCOMBE</div>
      <div class="role">MARKETING MANAGER</div>
      <div class="line"><span class="label">PHONE :</span> +44 20 7946 0321</div>
      <div class="line"><span class="label">WEB :</span> www.marlowvane.com</div>
      <div class="line"><span class="label">ADDR :</span> 8 ASHBY LANE</div>
      <div class="line">LONDON EC1V 2NX</div>
    </div>

    <div class="date"><span class="label">DATE :</span> 26-July-2015</div>

    <div class="body-copy">
      <p>Lorem ipsum dolor sit amet, consectetur adipiscing elit, sed do eiusmod tempor incididunt ut labore et dolore magna aliqua. Quis ipsum suspendisse ultrices gravida. Risus commodo viverra maecenas accumsan lacus vel facilisis. Lorem ipsum dolor sit amet, consectetur adipiscing elit, sed do eiusmod tempor incididunt ut labore et dolore magna aliqua. Quis ipsum suspendisse ultrices gravida.</p>
      <p>Lorem ipsum dolor sit amet, consectetur adipiscing elit, sed do eiusmod tempor incididunt ut labore et dolore magna aliqua. Quis ipsum suspendisse ultrices gravida. Risus commodo viverra maecenas accumsan lacus vel facilisis. Lorem ipsum dolor sit amet, consectetur adipiscing elit, sed do eiusmod tempor incididunt ut labore et dolore magna aliqua. Quis ipsum suspendisse ultrices gravida. Risus commodo viverra maecenas accumsan lacus vel facilisis.</p>
      <p>Lorem ipsum dolor sit amet, consectetur adipiscing elit, sed do eiusmod tempor incididunt ut labore et dolore magna aliqua. Quis ipsum suspendisse ultrices gravida. Risus commodo viverra maecenas accumsan lacus vel facilisis. Lorem ipsum dolor sit amet, consectetur adipiscing elit, sed do eiusmod tempor incididunt ut labore et dolore magna aliqua. Quis ipsum suspendisse ultrices gravida. Risus commodo viverra maecenas accumsan lacus vel facilisis.</p>
    </div>

    <div class="signoff">
      <div class="signature" role="img" aria-label="Handwritten signature"></div>
      <div class="name">SIMON T. HALLOWAY</div>
      <div class="role">CREATIVE DESIGNER</div>
    </div>

    <div class="footer-contacts">
      <div class="item">
        <svg viewBox="0 0 24 24" aria-hidden="true"><path fill="var(--plum)" d="M6.6 10.8a15.1 15.1 0 0 0 6.6 6.6l2.2-2.2c.3-.3.7-.4 1-.2 1.1.4 2.3.6 3.6.6.6 0 1 .4 1 1V20c0 .6-.4 1-1 1A17 17 0 0 1 3 4c0-.6.4-1 1-1h3.5c.6 0 1 .4 1 1 0 1.3.2 2.5.6 3.6.1.3 0 .7-.2 1z"/></svg>
        <div>+44 20 7946 0188<br>+44 20 7946 0188</div>
      </div>
      <div class="item">
        <svg viewBox="0 0 24 24" aria-hidden="true"><g fill="none" stroke="var(--plum)" stroke-width="2"><circle cx="12" cy="12" r="10"/><ellipse cx="12" cy="12" rx="4.5" ry="10"/><line x1="2" y1="12" x2="22" y2="12"/><line x1="4" y1="7" x2="20" y2="7"/><line x1="4" y1="17" x2="20" y2="17"/></g></svg>
        <div>www.marlowvane.com<br>office@marlowvane.com</div>
      </div>
      <div class="item">
        <svg viewBox="0 0 24 24" aria-hidden="true"><path fill="var(--plum)" d="M12 2a7 7 0 0 0-7 7c0 5.3 7 13 7 13s7-7.7 7-13a7 7 0 0 0-7-7zm0 9.5a2.5 2.5 0 1 1 0-5 2.5 2.5 0 0 1 0 5z"/></svg>
        <div>27 Calder Street<br>London SE1 9QH</div>
      </div>
    </div>

    <svg class="corner" style="left:0;top:409px" width="367" height="110" viewBox="0 409 367 110" aria-hidden="true">
      <path d="M32 431 V493 H322" fill="none" stroke="var(--accent)" stroke-width="6" stroke-linejoin="round"/>
      <line x1="117" y1="502" x2="292" y2="502" stroke="var(--plum)" stroke-width="1.6"/>
      <line x1="367" y1="414" x2="296" y2="485" stroke="var(--plum)" stroke-width="5"/>
      <line x1="367" y1="433" x2="281" y2="519" stroke="var(--accent)" stroke-width="6"/>
      <polygon points="367,449 367,519 297,519" fill="var(--plum)"/>
    </svg>
  </section>

</body>
</html>
```